K SPIRES Business Card Design

Need a business card design for K Spires, we're a tower company - our main scope of work is to upgrade cellular sites: swap antennas, install new coax, fiber, replace mounts, etc. Mostly tower work.

would like to see a sharp business card design with our logo either on background or with tower image on the background - something describing our field not only in words but in images.

Target Market(s)

USA

Industry/Entity Type

Business

Contact Information for Business Card

Tarnek Obliva
Operations Manager
K Spires LLC

cell 555-318-2094
tarnek@k-spires-example.com

4185 Wexbridge Commerce Pkwy, Suite D
Norcross, GA, 30571

Requirements
Must have
• some tower related design
Nice to have
• some tower or cellular antennas on the background, if possible to compliment our logo...

```html
<!DOCTYPE html>
<html lang="en">
<head>
<meta charset="utf-8">
<title>K Spires Business Card</title>
<link rel="stylesheet" href="https://fonts.googleapis.com/css2?family=Merriweather:wght@400;700&display=swap">
<style>
  :root {
    --page-bg: #e9e6e1;
    --card-black: #050505;
    --card-glow: #1c1c1c;
    --ink-white: #f2f2f2;
    --ink-blue: #3b3791;
    --ink-green: #2f8a3a;
    --ink-grey: #6b6767;
  }
  * { margin: 0; padding: 0; box-sizing: border-box; }
  html, body {
    width: 1200px;
    height: 900px;
    overflow: hidden;
    background: var(--page-bg);
    font-family: "Merriweather", Georgia, serif;
  }
  .canvas {
    position: relative;
    width: 1200px;
    height: 900px;
  }
  .card {
    position: absolute;
    top: 302px;
    width: 520px;
    height: 296px;
    background: radial-gradient(ellipse at 60% 30%, var(--card-glow) 0%, var(--card-black) 70%);
    border-radius: 3px;
    box-shadow: 0 6px 18px rgba(0,0,0,0.25);
    overflow: hidden;
  }
  .card--front { left: 50px; }
  .card--back { left: 630px; }

  .contact-block {
    position: absolute;
    left: 34px;
    top: 36px;
    color: var(--ink-white);
  }
  .contact-name {
    font-size: 19px;
    font-weight: 700;
    letter-spacing: 0.2px;
  }
  .contact-role {
    font-size: 12px;
    color: var(--ink-blue);
    margin-top: 3px;
  }
  .contact-details {
    list-style: none;
    margin-top: 18px;
    font-size: 11.5px;
    line-height: 1.75;
  }
  .contact-details .label { color: var(--ink-green); }

  .brand-name {
    position: absolute;
    font-weight: 400;
    white-space: nowrap;
    line-height: 1;
  }
  .card--front .brand-name {
    right: 34px;
    bottom: 34px;
    font-size: 42px;
    color: var(--ink-blue);
  }
  .card--back .brand-name {
    left: 50%;
    top: 50%;
    transform: translate(-50%, -50%);
    font-size: 64px;
    color: var(--ink-grey);
  }
</style>
</head>
<body>
<main class="canvas">
  <section class="card card--front" aria-label="Business card front">
    <div class="contact-block">
      <h1 class="contact-name">Tarnek Obliva</h1>
      <p class="contact-role">Operations Manager</p>
      <ul class="contact-details">
        <li>4185 Wexbridge Commerce Pkwy, Suite D</li>
        <li>Norcross, GA, 30571</li>
        <li><span class="label">C:</span> 555-318-2094</li>
        <li>tarnek@k-spires-example.com</li>
      </ul>
    </div>
    <p class="brand-name">K Spires</p>
  </section>

  <section class="card card--back" aria-label="Business card back">
    <p class="brand-name">K Spires</p>
  </section>
</main>
</body>
</html>
```